Natural Light/Organic/Documentary Photography Business

I like a simple, approachable, feminine, earthy/organic feel. Earth/neutral tones, nothing too loud or obnoxious. I like the watercolor look. I don't want anything too trendy or something I'll get tired of after a couple months. As far as colors, I am much more a fan of cream/taupe/blue/green...not a fan of pink or purple at all.

Target Market(s)

Weddings & Families

Industry/Entity Type

Wedding Photography

Contact Information for Business Card

website, email, phone number

Font styles to use
Other font styles liked:
• Horizontes, Gotham

Colors

Designer to choose colors to be used in the design.

Requirements
Must have
• Website: www.mirelhatchway.com
• Phone: 418.629.5073
• Email: mirel@mirelhatchway.com
Nice to have
• I like the watercolor look but its not necessary. I like simple/earthy tones. Nothing too loud or distracting. Simple & feminine without being too girly. I like an approachable/soft feel.
• Instagram: www.instagram.com/mirelhatchwayphotography/
Should not have
• NO loud colors or design or pattern. I do not want a photo of a camera or lens or anything cheesy like that.

```html
<!DOCTYPE html>
<html lang="en">
<head>
<meta charset="utf-8">
<title>Mirel Hatchway Photography — Business Card</title>
<link rel="stylesheet" href="https://fonts.googleapis.com/css2?family=Montserrat:wght@300;400;500&family=Sacramento&display=swap">
<style>
  :root {
    --page: #ffffff;
    --panel: #ffffff;
    --frame: #8e857d;
    --ink: #8a7d72;
    --ink-soft: #9a8f86;
    --sage: #b7c0aa;
    --tan: #cbb39c;
    --peach: #e9caa9;
    --taupe: #bfb0a2;
    --cream: #f6f2ec;
  }
  * { margin: 0; padding: 0; box-sizing: border-box; }
  html, body {
    width: 1200px;
    height: 734px;
    overflow: hidden;
    background: var(--page);
  }
  .canvas {
    position: relative;
    width: 1200px;
    height: 734px;
    font-family: "Montserrat", Arial, sans-serif;
    color: var(--ink);
  }
  .card {
    position: absolute;
    left: 87px;
    top: 77px;
    width: 1033px;
    height: 579px;
    overflow: hidden;
  }
  .card__wash {
    position: absolute;
    inset: 0;
    background: linear-gradient(115deg, var(--sage) 0%, var(--tan) 30%, var(--peach) 50%, var(--taupe) 68%, var(--cream) 100%);
  }
  .card__panel {
    position: absolute;
    left: 133px;
    top: 117px;
    width: 765px;
    height: 347px;
    background: var(--panel);
    border: 1.5px solid var(--frame);
    text-align: center;
  }
  .brand__name {
    position: absolute;
    left: 0;
    right: 0;
    top: 34px;
    font-family: "Sacramento", "Brush Script MT", cursive;
    font-weight: 400;
    font-size: 92px;
    line-height: 1;
    letter-spacing: 4px;
    color: var(--ink);
  }
  .brand__tagline {
    position: absolute;
    left: 0;
    right: 0;
    top: 141px;
    font-weight: 400;
    font-size: 13px;
    letter-spacing: 8px;
    padding-left: 8px;
    color: var(--ink);
  }
  .contact {
    position: absolute;
    left: 0;
    right: 0;
    top: 214px;
    list-style: none;
    font-size: 15.5px;
    font-weight: 300;
    line-height: 29.5px;
    letter-spacing: 0.6px;
    color: var(--ink-soft);
  }
  .contact__label { font-weight: 500; color: var(--ink); }
  .contact__sep { padding: 0 5px; }
</style>
</head>
<body>
  <main class="canvas">
    <section class="card">
      <div class="card__wash" role="img" aria-label="Watercolour wash in sage, tan, peach and cream tones"></div>
      <div class="card__panel">
        <h1 class="brand__name">Mirel Hatchway</h1>
        <p class="brand__tagline">PHOTOGRAPHY</p>
        <ul class="contact">
          <li><span class="contact__label">Website</span><span class="contact__sep">|</span>www.mirelhatchway.com&nbsp;&nbsp;-&nbsp;&nbsp;<span class="contact__label">Phone</span><span class="contact__sep">|</span>418 629 5073</li>
          <li><span class="contact__label">Email</span><span class="contact__sep">|</span>mirel@mirelhatchway.com</li>
          <li><span class="contact__label">Instagram</span><span class="contact__sep">|</span>@mirelhatchwayphotography</li>
        </ul>
      </div>
    </section>
  </main>
</body>
</html>
```